The Vantor Codex Book Cover

"The Vantor Codex" is a book I wrote with the slogan "Unlock Performance, Spark Engagement: Master the Art of Building Winning Cultures in Today's Hybrid World". The book is designed around a methodology that's mine and that I attached. I would love to see the graphic of the methodology integrated in the design in a very subtle way. Use colors from the model but the book cover should be catchy, modern and engaging to the eye.
Overall the book is about three key elements towards success:
- (Self) Directions (purpose)
- Human experience (people and psychological safety)
- Maximize engagement
The methodology is a FLOW so flow is something that could be incorporated as well in the concept.
Low design quality
Managers and Teams

```html
<!DOCTYPE html>
<html lang="en">
<head>
<meta charset="UTF-8">
<title>The Vantor Codex – Book Cover</title>
<link href="https://fonts.googleapis.com/css2?family=Montserrat:wght@400;500;700;900&display=swap" rel="stylesheet">
<style>
  :root {
    --ink: #0b0b0b;
    --brand-blue: #03a0da;
    --navy: #0a4f8a;
    --orange: #fb9a3f;
    --sun: #fbdc6d;
    --paper: #ffffff;
  }
  html, body {
    margin: 0;
    padding: 0;
    overflow: hidden;
    background: var(--paper);
  }
  .cover {
    position: relative;
    width: 933px;
    height: 1200px;
    overflow: hidden;
    background: var(--paper);
    font-family: "Montserrat", sans-serif;
    color: var(--ink);
  }
  .top-tab {
    position: absolute;
    left: 81px;
    top: 0;
    width: 107px;
    height: 48px;
    background: var(--brand-blue);
  }
  .tagline {
    position: absolute;
    left: 71px;
    top: 88px;
    margin: 0;
    font-size: 21px;
    font-weight: 400;
    letter-spacing: 0.42em;
    white-space: nowrap;
  }
  .title {
    position: absolute;
    left: 64px;
    top: 148px;
    margin: 0;
    line-height: 1;
    text-transform: uppercase;
  }
  .title span { display: block; }
  .title-lead {
    font-size: 112px;
    font-weight: 700;
    letter-spacing: 0.01em;
  }
  .title-main {
    margin-top: -10px;
    font-size: 142px;
    font-weight: 900;
    color: var(--brand-blue);
    letter-spacing: 0.005em;
  }
  .title-end {
    margin-top: -2px;
    font-size: 92px;
    font-weight: 500;
    letter-spacing: 0.02em;
  }
  .divider {
    position: absolute;
    left: 65px;
    top: 538px;
    width: 156px;
    height: 16px;
    background: var(--brand-blue);
  }
  .subtitle {
    position: absolute;
    left: 69px;
    top: 578px;
    margin: 0;
    font-size: 28.5px;
    font-weight: 700;
    line-height: 36px;
  }
  .byline {
    position: absolute;
    left: 72px;
    top: 830px;
    margin: 0;
    font-size: 30px;
    font-weight: 700;
  }
  .author {
    position: absolute;
    left: 70px;
    top: 876px;
    margin: 0;
    font-size: 56px;
    font-weight: 400;
    line-height: 66px;
    letter-spacing: 0.36em;
    white-space: nowrap;
  }
  .author span { display: block; }
  .flow-art {
    position: absolute;
    left: 402px;
    top: 518px;
    width: 472px;
    height: 682px;
  }
</style>
</head>
<body>
  <main class="cover">
    <div class="top-tab"></div>
    <p class="tagline">UNLOCK PERFORMANCE, SPARK ENGAGEMENT:</p>

    <h1 class="title">
      <span class="title-lead">The</span>
      <span class="title-main">Vantor</span>
      <span class="title-end">Codex</span>
    </h1>

    <div class="divider"></div>

    <p class="subtitle">Master the Art of<br>Building Winning<br>Cultures in Today's<br>Hybrid World</p>

    <p class="byline">by</p>
    <p class="author"><span>JORIS</span><span>KESSEL</span></p>

    <svg class="flow-art" viewBox="0 0 472 682" role="img"
         aria-label="Illustration of intertwining flowing ribbons in blue, navy, orange and yellow rising upward, with hands, devices, speech bubbles and small figures of managers and teams">
      <defs>
        <linearGradient id="flowTones" x1="0" y1="1" x2="0.6" y2="0">
          <stop offset="0" stop-color="#fbdc6d"/>
          <stop offset="0.35" stop-color="#fb9a3f"/>
          <stop offset="0.7" stop-color="#03a0da"/>
          <stop offset="1" stop-color="#0a4f8a"/>
        </linearGradient>
      </defs>
      <path d="M120 682 C 60 560, 150 470, 110 360 C 80 270, 170 190, 250 120 C 300 70, 380 40, 440 10 L 470 60 C 400 110, 320 170, 290 260 C 260 350, 340 430, 330 520 C 320 600, 380 640, 400 682 Z"
            fill="url(#flowTones)" opacity="0.9"/>
    </svg>
  </main>
</body>
</html>
```